Business Card Design

I run an executive search and head hunting company.
My areas of business is within financial services and I cover, primarily sales and trading.

I am looking for a double sided, black business card and would like to keep the design fairly simple. Name to front and details on the reverse.

I would require a logo - some logo ideas.

*****Just some idea I am playing with - a white out halo over the "i" in Corwin.
A quill or feather somewhere within the layout. Above the Corwin Tate & Pell ? beneath it ? etc......

I have attached something I quite like but the whole creativity and layout is down to you. I am thinking to have the "&" in between Corwin Tate & Pell, maybe white out perhaps and may have it spot gloss uv'd when it comes to print.

I am pretty open minded though !

Target Market(s)

financial services - brokers and investment banking

Industry/Entity Type

Financial

Contact Information for Business Card

Corwin Tate & Pell
No 7 The Yard
31 Larkfold Lane
Oakmere
Wexholt
RK29 8TQ

Telephone - + 44 (0)1388 604 517
Mobile -+ 44 (0) 7623 459 170
email - owen@corwintatepell.co.uk
web - www.corwintatepell.co.uk

Owen Pell
Managing Director

Colors

Designer to choose colors to be used in the design.

Requirements
Should not have
• Finance - brokers investment banking.

```html
<!DOCTYPE html>
<html lang="en">
<head>
<meta charset="utf-8">
<title>Corwin Tate &amp; Pell — Business Card</title>
<link rel="stylesheet" href="https://fonts.googleapis.com/css2?family=Bebas+Neue&family=Source+Sans+3:wght@400;600;700&display=swap">
<style>
  :root {
    --page: #ffffff;
    --card: #131313;
    --card-edge: #2a2a2a;
    --ink: #a9a9ab;
    --ink-soft: #9c9c9e;
  }
  html, body {
    margin: 0;
    padding: 0;
    width: 1200px;
    height: 999px;
    overflow: hidden;
    background: var(--page);
  }
  .canvas {
    position: relative;
    width: 1200px;
    height: 999px;
  }
  .card {
    position: absolute;
    width: 794px;
    height: 453px;
    background: radial-gradient(ellipse at 50% 50%, #161616 0%, var(--card) 70%, #0f0f0f 100%);
    box-shadow: inset 0 2px 0 var(--card-edge), inset 0 0 6px rgba(255,255,255,0.04);
  }
  .card--front { left: 79px; top: 35px; }
  .card--back  { left: 238px; top: 512px; }

  .wordmark {
    position: absolute;
    left: 0;
    right: 0;
    top: 190px;
    margin: 0;
    text-align: center;
    font-family: "Bebas Neue", "Oswald", sans-serif;
    font-weight: 400;
    font-size: 77px;
    line-height: 1;
    letter-spacing: 1px;
    color: var(--ink);
  }

  .holder {
    position: absolute;
    left: 60px;
    top: 363px;
    font-family: "Source Sans 3", "Myriad Pro", sans-serif;
    color: var(--ink);
  }
  .holder__name {
    margin: 0;
    font-weight: 700;
    font-size: 24px;
    line-height: 30px;
  }
  .holder__role {
    margin: 0;
    font-weight: 400;
    font-size: 19.5px;
    line-height: 25px;
  }

  .contact {
    position: absolute;
    left: 396px;
    top: 206px;
    font-family: "Source Sans 3", "Myriad Pro", sans-serif;
    font-style: normal;
    font-size: 20px;
    color: var(--ink);
  }
  .contact__row {
    position: relative;
    padding-left: 42px;
    line-height: 26.5px;
  }
  .contact__row--address { margin-bottom: 23px; }
  .contact__icon {
    position: absolute;
    left: 0;
    top: 4px;
    width: 20px;
    height: 20px;
    fill: var(--ink-soft);
  }
  .contact__row--address .contact__icon { top: 4px; width: 20px; height: 34px; }
</style>
</head>
<body>
<main class="canvas">

  <section class="card card--front" aria-label="Card front">
    <h1 class="wordmark">CORWIN TATE &amp; PELL</h1>
  </section>

  <section class="card card--back" aria-label="Card back">
    <div class="holder">
      <p class="holder__name">Owen Pell</p>
      <p class="holder__role">Managing Director</p>
    </div>

    <address class="contact">
      <div class="contact__row contact__row--address">
        <svg class="contact__icon" viewBox="0 0 20 34" aria-hidden="true">
          <path d="M10 0C4.5 0 0 4.4 0 9.8 0 16.8 10 34 10 34s10-17.2 10-24.2C20 4.4 15.5 0 10 0zm0 14a4.2 4.2 0 1 1 0-8.4 4.2 4.2 0 0 1 0 8.4z"/>
        </svg>
        Corwin Tate &amp; Pell No 7<br>
        The Yard 31 Larkfold Lane<br>
        Oakmere Wexholt RK29 8TQ
      </div>
      <div class="contact__row">
        <svg class="contact__icon" viewBox="0 0 20 20" aria-hidden="true">
          <path d="M4.2 1.5 7 4.8c.4.5.4 1.2-.1 1.7L5.5 7.9c1 2.3 3.9 5.2 6.3 6.3l1.4-1.4c.5-.5 1.2-.5 1.7-.1l3.3 2.8c.5.4.5 1.2.1 1.7l-1.6 1.6c-.9.9-2.3 1.2-3.5.7C7.8 17.6 2.4 12.2.5 6.8.1 5.6.4 4.2 1.3 3.3L2.5 1.5c.5-.5 1.3-.5 1.7 0z"/>
          <path d="M12 2a6 6 0 0 1 6 6h-1.6A4.4 4.4 0 0 0 12 3.6zm0 3a3 3 0 0 1 3 3h-1.6A1.4 1.4 0 0 0 12 6.6z"/>
        </svg>
        + 44 (0)1388 604 517
      </div>
      <div class="contact__row">
        <svg class="contact__icon" viewBox="0 0 20 20" aria-hidden="true">
          <path d="M3 1h14v18H3zm2 2v14h10V3zm2.5 10.5 5-5 .9.9-5 5z"/>
        </svg>
        07623 459 170
      </div>
      <div class="contact__row">
        <svg class="contact__icon" viewBox="0 0 20 20" aria-hidden="true">
          <path d="M10 2 1 8v10h18V8zm0 2.3 6.3 4.2L10 12.4 3.7 8.5zM3 10.5l7 4.3 7-4.3V16H3z"/>
        </svg>
        owen@corwintatepell.co.uk
      </div>
      <div class="contact__row">
        <svg class="contact__icon" viewBox="0 0 20 20" aria-hidden="true">
          <path d="M10 1a9 9 0 1 0 0 18 9 9 0 0 0 0-18zm-1 2.2v3.3H6.3C7 4.8 7.9 3.6 9 3.2zm2 0c1.1.4 2 1.6 2.7 3.3H11zM4.6 5.2h0c.3-.3.7-.6 1-.8-.3.6-.5 1.3-.7 2.1H3.7c.3-.5.6-.9.9-1.3zm10.8 0c.3.4.6.8.9 1.3h-1.2c-.2-.8-.4-1.5-.7-2.1.4.2.7.5 1 .8zM3.1 8.5h1.6v3H3.1zm3.6 0H9v3H6.7zm4.3 0h2.3v3H11zm4.3 0h1.6v3h-1.6zM3.7 13.5h1.2c.2.8.4 1.5.7 2.1-.8-.5-1.4-1.2-1.9-2.1zm2.6 0H9v3.3c-1.1-.4-2-1.6-2.7-3.3zm4.7 0h2.7c-.7 1.7-1.6 2.9-2.7 3.3zm4.1 0h1.2c-.5.9-1.1 1.6-1.9 2.1.3-.6.5-1.3.7-2.1z"/>
        </svg>
        www.corwintatepell.co.uk
      </div>
    </address>
  </section>

</main>
</body>
</html>
```